Business card design for Keldor Engineering Tandem

We need a new business card design along with all the necessary to place an order. The company is Keldor Engineering Tandem and we recently updated our logo.

```html
<!DOCTYPE html>
<html lang="en">
<head>
<meta charset="utf-8">
<title>Keldor Engineering Tandem – Business Card</title>
<link rel="stylesheet" href="https://fonts.googleapis.com/css2?family=Kanit:wght@400;600&display=swap">
<style>
  :root {
    --canvas-bg: #3b3b3c;
    --card-dark: #1c1c1c;
    --brand-yellow: #e2bf25;
    --brand-yellow-deep: #c9a71c;
    --text-light: #f2f2f2;
    --logo-grey: #9a9a9a;
  }
  * { box-sizing: border-box; margin: 0; padding: 0; }
  html, body {
    width: 1200px; height: 1059px; overflow: hidden;
    background: var(--canvas-bg);
    font-family: "Kanit", sans-serif;
  }
  .canvas { position: relative; width: 1200px; height: 1059px; }
  .card {
    position: absolute; left: 256px; width: 688px; height: 394px;
    border-radius: 26px; overflow: hidden;
  }
  .card--front { top: 100px; background: var(--card-dark); }
  .card--back { top: 536px; background: var(--brand-yellow); }

  .brand-lockup {
    position: absolute; left: 32px; top: 180px;
    display: flex; align-items: center; gap: 10px;
  }
  .brand-lockup__mark { width: 16px; height: 16px; background: var(--brand-yellow); flex: none; }
  .brand-lockup__name {
    font-size: 21px; font-weight: 400; color: var(--logo-grey);
    letter-spacing: 0.3px; white-space: nowrap;
  }

  .divider {
    position: absolute; left: 340px; top: 82px;
    width: 2px; height: 229px; background: var(--brand-yellow);
  }
  .details { position: absolute; left: 357px; top: 76px; color: var(--text-light); }
  .details__name {
    font-size: 31px; font-weight: 600; color: var(--brand-yellow);
    line-height: 36px; letter-spacing: 0.2px; white-space: nowrap;
  }
  .details__title { font-size: 18px; font-weight: 400; line-height: 24px; margin-top: 1px; }
  .details__address { margin-top: 22px; font-size: 18px; line-height: 27px; white-space: nowrap; }
  .contact-list { list-style: none; margin-top: 20px; font-size: 18px; }
  .contact-list li { display: flex; align-items: center; height: 27px; gap: 8px; white-space: nowrap; }
  .contact-list svg { width: 16px; height: 16px; fill: var(--brand-yellow); flex: none; }

  .back-name {
    position: absolute; inset: 0; display: flex;
    align-items: center; justify-content: center;
    font-size: 30px; font-weight: 400; color: var(--brand-yellow-deep);
    letter-spacing: 0.5px;
  }
</style>
</head>
<body>
<main class="canvas">
  <section class="card card--front">
    <div class="brand-lockup">
      <span class="brand-lockup__mark"></span>
      <span class="brand-lockup__name">Keldor Engineering Tandem</span>
    </div>
    <div class="divider"></div>
    <div class="details">
      <h1 class="details__name">OWEN HARTLEY</h1>
      <p class="details__title">Managing Director</p>
      <p class="details__address">Keldor Engineering Tandem<br>27 Larkfield Road, Kestbury KB4 2TW</p>
      <ul class="contact-list">
        <li>
          <svg viewBox="0 0 16 16" aria-hidden="true"><path d="M2 6c0-2 2.5-3 6-3s6 1 6 3v1h-3V5.5H5V7H2z"/><path d="M4 8l1.5-2h5L12 8v5H4z"/></svg>
          01632 960418
        </li>
        <li>
          <svg viewBox="0 0 16 16" aria-hidden="true"><path d="M1 3h14v1.5L8 9 1 4.5z"/><path d="M1 6.2l7 4.5 7-4.5V13H1z"/></svg>
          sales@keldorengineering.co.uk
        </li>
        <li>
          <svg viewBox="0 0 16 16" aria-hidden="true"><circle cx="8" cy="8" r="7"/><path d="M4 4.5c1.5 0 2.5 1 2 2.5S4 8.5 4.5 10 3 11 2.5 9.5M10 3c.5 1.5 2 1.5 2.5 3s-1 2-1 3.5.5 2 1.5 2.5" stroke="#1c1c1c" stroke-width="1.2" fill="none"/></svg>
          www.keldorengineering.co.uk
        </li>
      </ul>
    </div>
  </section>

  <section class="card card--back">
    <p class="back-name">Keldor Engineering Tandem</p>
  </section>
</main>
</body>
</html>
```